One page flyer for nonprofit focused IT company

I need a one page flyer (one side of a single 8.5x11 page) with text and graphics. The company logo is already done, and it must appear on the flyer along with other icons and graphics. The final design will be printed on heavy weight glossy paper as a handout and also distributed as a PDF.

The text is provided in an attachment, if it needs to be shortened let me know.

Industry/Entity Type

Information Technology

Requirements
Must have
• some flare (colors, icons or images)
Should not have
• While we work for nonprofits, my company is a FOR PROFIT company.

```html
<!DOCTYPE html>
<html lang="en">
<head>
<meta charset="utf-8">
<title>Northfield Data Corporation – Nonprofit IT Services</title>
<link rel="stylesheet" href="https://fonts.googleapis.com/css2?family=Montserrat:wght@300;400;700;800&family=Arimo:wght@400&display=swap">
<style>
  :root{
    --brand-red:#931a2c;
    --ink:#231f20;
    --body:#1e1e1e;
    --white:#ffffff;
    --footer-dark:#2a2627;
    --photo-deep:#1f3550;
    --photo-mid:#5f7b99;
    --photo-warm:#a88f7f;
  }
  *{box-sizing:border-box;margin:0;padding:0}
  html,body{width:945px;height:1200px;overflow:hidden;background:var(--white)}
  .flyer{position:relative;width:945px;height:1200px;background:var(--white);font-family:"Arimo",Arial,sans-serif;color:var(--body)}

  /* Brand block */
  .brand{position:absolute;left:55px;top:39px;width:308px;text-align:center}
  .brand-square{display:block;width:44px;height:44px;margin:0 auto 22px;background:var(--brand-red)}
  .brand-name{font-family:"Montserrat",sans-serif;font-weight:700;color:var(--brand-red);font-size:20px;letter-spacing:1px;line-height:1.35}

  /* Headline */
  .headline{position:absolute;left:489px;top:58px;font-family:"Montserrat",sans-serif;font-weight:800;color:var(--ink);line-height:1}
  .headline .line{display:block;font-size:36px;letter-spacing:-.5px;margin-bottom:7px}
  .headline .accent{color:var(--brand-red);font-size:50px;margin-top:3px;letter-spacing:0}

  /* Intro panel */
  .intro{position:absolute;left:0;top:191px;width:420px;height:428px;background:var(--brand-red);color:var(--white);padding:26px 30px 0 55px}
  .intro h2{font-family:"Montserrat",sans-serif;font-weight:800;font-size:22px;line-height:27px;margin-bottom:22px}
  .intro p{font-family:"Montserrat",sans-serif;font-weight:300;font-size:13.9px;line-height:19.4px}

  .hero-photo{position:absolute;left:420px;top:233px;width:525px;height:386px;
    background:radial-gradient(circle at 60% 50%,rgba(255,255,255,.75) 0,rgba(200,220,240,.35) 12%,transparent 30%),
    linear-gradient(120deg,var(--photo-warm) 0%,var(--photo-mid) 45%,var(--photo-deep) 100%)}

  /* Section labels */
  .section-label{position:absolute;background:var(--brand-red);color:var(--white);font-family:"Montserrat",sans-serif;font-weight:800;font-size:18px;height:33px;line-height:33px;padding:0 14px}
  .label-successes{left:53px;top:642px;width:168px}
  .label-solutions{left:476px;top:640px;width:164px}

  /* Successes */
  .successes{position:absolute;left:52px;top:704px;width:370px}
  .success{margin-bottom:16px}
  .success h3,.solution h3{font-family:"Montserrat",sans-serif;font-weight:800;color:var(--brand-red);font-size:14.5px;line-height:16px;margin-bottom:2px}
  .success p,.solution p{font-size:11.6px;line-height:17.5px;color:var(--body)}

  /* Solutions */
  .solution{position:absolute;left:469px;width:440px;padding-left:65px}
  .solution .icon{position:absolute;left:0;top:0;width:56px;height:56px;border-radius:50%;background:var(--brand-red);display:flex;align-items:center;justify-content:center}
  .solution .icon svg{width:32px;height:32px;fill:none;stroke:var(--white);stroke-width:1.6;stroke-linecap:round;stroke-linejoin:round}

  /* Footer */
  .footer-web{position:absolute;left:0;top:1141px;width:433px;height:59px;background:var(--brand-red);color:var(--white);display:flex;align-items:center;justify-content:center;gap:10px;font-family:"Montserrat",sans-serif;font-weight:800;font-size:17px}
  .footer-contact{position:absolute;left:433px;top:1164px;width:512px;height:36px;background:var(--footer-dark);color:var(--white);display:flex;align-items:center;gap:28px;padding-left:54px;font-family:"Montserrat",sans-serif;font-weight:400;font-size:13.5px;letter-spacing:.3px}
  .footer-contact span{display:flex;align-items:center;gap:8px}
  .footer-web svg,.footer-contact svg{fill:none;stroke:var(--white);stroke-width:1.8;stroke-linecap:round;stroke-linejoin:round}
</style>
</head>
<body>
<main class="flyer">

  <header class="brand">
    <span class="brand-square"></span>
    <div class="brand-name">NORTHFIELD DATA<br>CORPORATION</div>
  </header>

  <h1 class="headline">
    <span class="line">50 YEARS</span>
    <span class="line">OF NONPROFIT</span>
    <span class="line accent">IT SERVICES</span>
  </h1>

  <section class="intro">
    <h2>An Efficient and<br>Elegant Approach<br>to IT Solution<br>Implementations</h2>
    <p>Northfield Data Corporation has been supporting the Information Systems needs of nonprofits for over 50 years. We continually strive to bring the latest technologies and best practices to nonprofits to drive down the cost of IT while implementing systems that drive revenue. Our Agile approach to IT management means that we deliver working systems to every one of our clients every two weeks.</p>
  </section>

  <div class="hero-photo" role="img" aria-label="Photo of a hand holding a smartphone with a glowing network globe and connected app icons floating above it"></div>

  <div class="section-label label-successes">SUCCESSES</div>
  <div class="section-label label-solutions">SOLUTIONS</div>

  <section class="successes">
    <article class="success">
      <h3>90% Reduction in Software Development Costs</h3>
      <p>Halvorsen Ratings’ National Vehicle Retailers Guild needed to update their core product offering; they engaged their in-house IT department who estimated the project would take 3 years at a cost of $3,000,000. NVRG decided to work with Northfield Data Corporation instead, and the product was released to production in only 9 months at one tenth of the cost, only $300,000</p>
    </article>
    <article class="success">
      <h3>10x Increase in Membership</h3>
      <p>Greenway Paths Alliance needed to move to online membership registration and contracted with Northfield Data Corporation to build a significant online presence and engage potential members. Through compelling online tools and mobile applications Greenway Paths has increased membership 10 fold.</p>
    </article>
    <article class="success">
      <h3>20% Reduction in Overhead</h3>
      <p>The National Council for Civic Equity had antiquated systems and processes in place to manage over 500 chapters across the nation. Working with NDC they implemented online tools to allow communication and management between the local chapters and national headquarters. This eliminated much of the overhead of chapter management, reducing HR costs by 20%.</p>
    </article>
  </section>

  <article class="solution" style="top:676px">
    <div class="icon"><svg viewBox="0 0 32 32"><rect x="3" y="6" width="18" height="13" rx="1"/><path d="M9 23h6M12 19v4"/><rect x="20" y="10" width="9" height="16" rx="1.5"/><path d="M8 11l-2 2 2 2M16 11l2 2-2 2"/></svg></div>
    <h3>Web Applications</h3>
    <p>With a focus on non-profit websites and web based applications, NDC helps nonprofits communicate with their members and donors while maximizing online giving and engagement.</p>
  </article>

  <article class="solution" style="top:764px">
    <div class="icon"><svg viewBox="0 0 32 32"><rect x="9" y="3" width="14" height="26" rx="2"/><path d="M9 7h14M9 25h14"/><circle cx="16" cy="16" r="3.5"/><path d="M16 10.5v2M16 19.5v2M10.5 16h2M19.5 16h2"/></svg></div>
    <h3>Mobile Applications</h3>
    <p>Northfield Data Corporation implements mobile applications for all major mobile platforms to provide direct communications with members and donors enabling real-time, two way interaction.</p>
  </article>

  <article class="solution" style="top:851px">
    <div class="icon"><svg viewBox="0 0 32 32"><circle cx="12" cy="16" r="4"/><circle cx="12" cy="16" r="8"/><path d="M20 16h5M18 10l5-3M18 22l5 3"/><circle cx="26" cy="16" r="1.5"/><circle cx="24.5" cy="6.5" r="1.5"/><circle cx="24.5" cy="25.5" r="1.5"/></svg></div>
    <h3>Systems Integration</h3>
    <p>Every nonprofit’s IT applications are scattered and disconnected. Northfield Data Corporation has decades of experience integrating these applications into a single cohesive system.</p>
  </article>

  <article class="solution" style="top:938px">
    <div class="icon"><svg viewBox="0 0 32 32"><path d="M5 27h22"/><rect x="7" y="17" width="4" height="10"/><rect x="14" y="11" width="4" height="16"/><rect x="21" y="6" width="4" height="21"/></svg></div>
    <h3>Business Intelligence and Reporting</h3>
    <p>Northfield Data Corporation can wrestle all of an organization’s data into simple executive dashboards and reports.</p>
  </article>

  <article class="solution" style="top:1008px">
    <div class="icon"><svg viewBox="0 0 32 32"><path d="M9 23a5 5 0 0 1-.5-10 7 7 0 0 1 13.5-1.5A5.5 5.5 0 0 1 23 23z"/></svg></div>
    <h3>Cloud Migration</h3>
    <p>Reduce IT costs by migrating to the latest cloud solutions.</p>
  </article>

  <article class="solution" style="top:1060px">
    <div class="icon"><svg viewBox="0 0 32 32"><ellipse cx="16" cy="8" rx="9" ry="3"/><path d="M7 8v16c0 1.7 4 3 9 3s9-1.3 9-3V8M7 16c0 1.7 4 3 9 3s9-1.3 9-3"/></svg></div>
    <h3>Member Donor Database</h3>
    <p>Northfield Data Corporation’s GiveLedger Member / Donor CRM system is fully customized for each client meeting the unique needs of your organization.</p>
  </article>

  <footer>
    <div class="footer-web">
      <svg width="22" height="22" viewBox="0 0 24 24"><circle cx="12" cy="12" r="10"/><path d="M2 12h20M12 2c3 3 3 17 0 20M12 2c-3 3-3 17 0 20"/></svg>
      www.northfielddata.com
    </div>
    <div class="footer-contact">
      <span><svg width="18" height="18" viewBox="0 0 24 24"><path d="M5 3h4l2 5-2.5 1.5a11 11 0 0 0 6 6L16 13l5 2v4a2 2 0 0 1-2 2A16 16 0 0 1 3 5a2 2 0 0 1 2-2z"/></svg>010 48 21 70 93</span>
      <span><svg width="18" height="16" viewBox="0 0 24 20"><rect x="2" y="3" width="20" height="14" rx="1"/><path d="M2 4l10 7 10-7"/></svg>mail@northfielddata.com</span>
    </div>
  </footer>

</main>
</body>
</html>
```